Business Card Design for Vintage Jazz

I am a vintage jazz band leader in New York City. My groups play the music of the 1920s, 1930s and 1940s. My website is morvalquist.com for more info on what I do.

I am looking for a two sided business card design that has the look and feel of a really nice business card from the 1930s. I need to convey with the design that my work has that vintage kind of class and style, but also conveys that we are fun and entertaining.

Most importantly it should make a bold staement. If Hal Denbrook had a card, what would it have looked like? I want a card that I feel confident will make an impact and will let people know that my work is te the top that NYC has to offer in vintage jazz..

Note that I have only decided to avoid the "committed payment" option as I have not used this service before. Assuming that I get quality work I will select a design from those presented.

Target Market(s)

people who want to hire my band for events, media, and new fans of the band

Industry/Entity Type

Performing Art

Contact Information for Business Card

Definitely a matte finish, possibly a sort of old style of paper with that brown tint? definitely a thick card.

Requirements
Must have
• FRONT
• My name: Tobin Vashley
• What I do: Bandleader, Guitarist, Vocalist, Songwriter
• Contact Details: morvalquist.com tobin@morvalquist.com 646-555-0148
• BACK
• My Social Media Links:
• fans.morvalquist.com
• twitter, instagram, linkedin: morvalquist
• I'm also including a photo image I would like to use. The photo's background is not needed, and to be honest isn't really desireable. Just looking to use the image of me.
Nice to have
• I'm attaching which could be used as is, omitted from the card, or altered maybe with text going around the outside of the circle or in some other way. It may need some clean up to the edges of the lettering as we only use it for the website thumbnail.
• If there's space I'd like to include the text "join our mailing list for a free song download: freesong.morvalquist.com" If not perhaps just "Download a Free Song at: freesong.morvalquist.com - something to this end.
Should not have
• anything cartoony. Don't think retro 90s's vision of the swing era, think actual swing era!
• anything modern. Got to look old school
• Try to avoid dark backgrounds. Since we often play in bars and clubs where it is dar, a d
• avoid script fonts.

```html
<!DOCTYPE html>
<html lang="en">
<head>
<meta charset="utf-8">
<title>Tobin Vashley – Business Card</title>
<link href="https://fonts.googleapis.com/css2?family=Open+Sans:wght@400;600;700&display=swap" rel="stylesheet">
<style>
  :root {
    --backdrop: #e6e6e6;
    --card: #ffffff;
    --ink: #111111;
    --paper-text: #ffffff;
    --shadow: rgba(0,0,0,0.18);
  }
  * { box-sizing: border-box; margin: 0; padding: 0; }
  html, body {
    width: 1200px; height: 900px; overflow: hidden;
    background: var(--backdrop);
    font-family: "Open Sans", Arial, sans-serif;
  }
  .canvas { position: relative; width: 1200px; height: 900px; }
  .card {
    position: absolute; left: 250px; width: 700px; height: 400px;
    background: var(--card); border-radius: 28px; overflow: hidden;
    box-shadow: 0 10px 30px var(--shadow);
  }
  .card--back { top: 40px; }
  .card--front { top: 460px; }
  .band { position: absolute; background: var(--ink); }

  /* Back */
  .card--back .band { left: 0; right: 0; top: 118px; height: 104px; }
  .promo { position: absolute; left: 48px; top: 145px; color: var(--paper-text); }
  .promo__title { font-weight: 700; font-size: 22px; letter-spacing: 1px; text-transform: uppercase; }
  .promo__url { font-size: 16px; letter-spacing: 0.5px; margin-top: 4px; }
  .social-handle { position: absolute; right: 60px; top: 252px; font-size: 17px; color: var(--ink); display: flex; align-items: center; gap: 10px; }
  .social-handle__dot { width: 12px; height: 12px; border-radius: 50%; background: var(--ink); }
  .social-page { position: absolute; left: 48px; top: 330px; font-size: 17px; color: var(--ink); display: flex; align-items: center; gap: 10px; }
  .social-page__square { width: 12px; height: 12px; background: var(--ink); }

  /* Monogram seal */
  .seal {
    position: absolute; width: 196px; height: 196px; border-radius: 50%;
    background: var(--ink); border: 5px solid var(--card); outline: 4px solid var(--ink);
    display: flex; align-items: center; justify-content: center; text-align: center;
    color: var(--paper-text); font-weight: 600; font-size: 22px; line-height: 1.15; letter-spacing: 0.5px;
  }
  .card--back .seal { right: 60px; top: 40px; }

  /* Front */
  .card--front .band--top { left: 420px; right: 0; top: 70px; height: 96px; }
  .card--front .seal { right: 60px; top: 20px; }
  .identity { position: absolute; left: 0; width: 520px; top: 176px; text-align: center; color: var(--ink); }
  .identity__name { font-weight: 700; font-size: 30px; letter-spacing: 1px; text-transform: uppercase; }
  .identity__role { font-size: 15px; letter-spacing: 0.5px; text-transform: uppercase; margin-top: 2px; }
  .card--front .band--bottom { left: 0; right: 0; top: 260px; height: 96px; }
  .contact { position: absolute; left: 48px; top: 268px; color: var(--paper-text); font-size: 16px; line-height: 26px; }
  .contact b { font-weight: 700; }
</style>
</head>
<body>
<div class="canvas">

  <section class="card card--back" aria-label="Card back">
    <div class="band"></div>
    <div class="promo">
      <p class="promo__title">Download a free song at</p>
      <p class="promo__url">www.freesong.morvalquist.com</p>
    </div>
    <div class="seal">Tobin<br>Vashley</div>
    <p class="social-handle"><span class="social-handle__dot"></span>morvalquist</p>
    <p class="social-page"><span class="social-page__square"></span>fans.morvalquist.com</p>
  </section>

  <section class="card card--front" aria-label="Card front">
    <div class="band band--top"></div>
    <div class="seal">Tobin<br>Vashley</div>
    <div class="identity">
      <h1 class="identity__name">Tobin Vashley</h1>
      <p class="identity__role">Bandleader, Guitarist, Vocalist, Songwriter</p>
    </div>
    <div class="band band--bottom"></div>
    <div class="contact">
      <p><b>P:</b> 646-555-0148</p>
      <p><b>E:</b> tobin@morvalquist.com</p>
      <p><b>W:</b> www.morvalquist.com</p>
    </div>
  </section>

</div>
</body>
</html>
```